Water ATM Card

Need a design for water ATM cards. Size of card is 3.375 x 2.125 inch
On the Front include the Cedar hollow Logo.
Bottom right corner should have Price $100
On the Back
This card is to be used to access water refills at any Cedar Hollow Water Vending Machines.
Please contact (869) 418 2930 or (869) 534 1276 or email clearflowbox@mailvista.example for any assistance or recharging of card.

```html
<!DOCTYPE html>
<html lang="en">
<head>
<meta charset="utf-8">
<title>Cedar Hollow Water Card</title>
<link href="https://fonts.googleapis.com/css2?family=Poppins:ital,wght@0,300;0,400;0,500;0,600;0,700;1,600&family=Montserrat:wght@700&display=swap" rel="stylesheet">
<style>
  :root {
    --page-bg: #e9ecef;
    --card-white: #ffffff;
    --brand-blue: #1a6fbe;
    --tag-blue: #2a5aa8;
    --back-blue: #1877c0;
    --back-blue-deep: #1368ad;
    --water-light: #dcecf8;
    --water-mid: #7fb6e2;
    --water-deep: #2f76b8;
    --price-green: #43a53c;
    --text-white: #ffffff;
  }
  * { margin: 0; padding: 0; box-sizing: border-box; }
  html, body {
    width: 1093px; height: 1200px; overflow: hidden;
    background: var(--page-bg);
    font-family: "Poppins", sans-serif;
  }
  .sheet { position: relative; width: 1093px; height: 1200px; }
  .card {
    position: absolute; left: 265px; width: 580px; height: 357px;
    border-radius: 24px; overflow: hidden;
  }
  .card-front { top: 226px; background: var(--card-white); }
  .card-back { top: 621px; background: linear-gradient(180deg, var(--back-blue) 0%, var(--back-blue-deep) 100%); color: var(--text-white); text-align: center; }

  .front-water {
    position: absolute; left: 0; right: 0; top: 128px; bottom: 0;
    background:
      linear-gradient(175deg, rgba(255,255,255,1) 0%, rgba(255,255,255,0) 30%),
      linear-gradient(172deg, var(--water-light) 20%, var(--water-mid) 48%, var(--water-deep) 62%, var(--water-mid) 72%, var(--water-light) 92%);
  }
  .brand { position: absolute; left: 20px; top: 86px; }
  .brand-name {
    font-family: "Montserrat", sans-serif; font-weight: 700;
    font-size: 33px; letter-spacing: 1px; color: var(--brand-blue);
    line-height: 1; text-transform: uppercase; white-space: nowrap;
  }
  .brand-tagline {
    margin: 6px 0 0 48px; font-weight: 400; font-size: 18px;
    color: var(--tag-blue); letter-spacing: 0.6px; line-height: 1;
  }
  .price-tag {
    position: absolute; right: 0; top: 261px; height: 43px; width: 168px;
    background: var(--price-green); border-radius: 22px 0 0 22px;
    color: var(--text-white); font-weight: 600; font-size: 22px;
    line-height: 43px; padding-left: 20px;
  }

  .back-water {
    position: absolute; left: 0; right: 0; top: 120px; bottom: 40px;
    background: linear-gradient(170deg, rgba(255,255,255,0) 10%, rgba(190,220,245,0.28) 45%, rgba(255,255,255,0.12) 70%, rgba(255,255,255,0) 95%);
  }
  .back-content { position: relative; padding-top: 84px; }
  .usage-note {
    font-weight: 700; font-size: 19.5px; line-height: 29px;
    text-transform: uppercase; letter-spacing: -0.2px;
  }
  .contact-label {
    display: flex; align-items: center; justify-content: center; gap: 10px;
    margin-top: 34px; font-weight: 300; font-size: 17px; line-height: 1;
  }
  .contact-label::before, .contact-label::after {
    content: ""; width: 140px; height: 1px; background: rgba(255,255,255,0.45);
  }
  .phones { margin-top: 13px; font-weight: 500; font-size: 23px; line-height: 1.2; }
  .joiner { font-weight: 400; font-size: 15px; margin: 0 3px; }
  .email-line { margin-top: 8px; font-size: 15px; }
  .email { font-style: italic; font-weight: 600; font-size: 21px; margin-left: 6px; }
  .help-note { margin-top: 2px; font-weight: 400; font-size: 17px; }
</style>
</head>
<body>
<div class="sheet">
  <section class="card card-front">
    <div class="front-water" role="img" aria-label="Photograph of a clear blue water splash"></div>
    <div class="brand">
      <div class="brand-name">Cedar Hollow</div>
      <div class="brand-tagline">Purified Spring Water</div>
    </div>
    <div class="price-tag">PRICE $100</div>
  </section>

  <section class="card card-back">
    <div class="back-water" role="img" aria-label="Faint photograph of flowing water"></div>
    <div class="back-content">
      <p class="usage-note">This card is to be used to<br>access water refills at any Cedar<br>Hollow water vending machines</p>
      <p class="contact-label">Please contact</p>
      <p class="phones">(869) 418 2930<span class="joiner">or</span>(869) 534 1276</p>
      <p class="email-line">or<span class="email">clearflowbox@mailvista.example</span></p>
      <p class="help-note">for any assistance or recharging of card</p>
    </div>
  </section>
</div>
</body>
</html>
```